VORNAK SYSTEMS BUSINESS CARD DESIGN

WE WANT COMPLETE NEW DESIGN OF OUR BUSINESS CARD. WE ARE AN INTEGRATION COMPANY, WHERE WE INTEGRATE IOT/SMART SYSTEMS TO HOMES AND CORPORATE CUSTOMERS. WE SUPPLY AND INSTALL AUTOMATION PRODUCTS. THE FINAL DESIGN SHOULD COMMUNICATE TECHNOLOGY. THE CARD DESIGN SHOULD BE VERY IMPACT FULL. LOGO NEEDS TO BE THERE. IT WOULD NICE IF THE DESIGN WAS CLEAN. COLORS IS UP TO DESIGNER TO PLAY WITH, OR CAN STICK TO CORPORATE COLORS (FOLLOW LOGO). I HAVE ADDED FEW REFERENCE PHOTOS TO DRAW INSPIRATION MAYBE. I HAVE ADDED A HEX DESIGN, ITS NOT NECESSARY TO USE THIS DESIGN, ITS UPTO DESIGNER, JUST ADDED IF NEEDED TO PLAY WITH DESIGN.

Target Market(s)

Private end users and corporate clients

Industry/Entity Type

technology, home automation, home theaters, building management systems, IOT

Contact Information for Business Card

It should include Employee name, personal number, office number, email address, both in English and arabic. DETAILS TO INCLUDE :RAJESH PALLIVAL, MOBILE 0097150738265,OFFCIE 009714368547, RAJESH@VORNAKSYS.EXAMPLE

Requirements
Must have
• Should feel like a technology company from design. Details both and in English and arabic (or at least have provision for arabic in design).
Nice to have
• I would like logo on one side, and details on the other side. Logo design side should communicate technology with logo. Other side can be clean just with information or also have some design aspects following from logo side. it would be interesting to see submissions with square design as well (that looks like an app Icon). colors could be of logo, red black grey and white. I have added some designs to draw inspiration from

```html
<!DOCTYPE html>
<html lang="en">
<head>
<meta charset="utf-8">
<title>Vornak Systems Business Card</title>
<link href="https://fonts.googleapis.com/css2?family=Arimo:wght@400;700&display=swap" rel="stylesheet">
<style>
  :root {
    --page: #161617;
    --card: #2f2f31;
    --card-back: #2a2a2c;
    --red: #e21b23;
    --grey: #9a9a9c;
    --white: #f2f2f2;
    --text: #ececec;
    --faint: #3a3a3c;
    --emboss: #3d3d40;
  }
  * { box-sizing: border-box; margin: 0; padding: 0; }
  html, body {
    width: 1200px; height: 963px; overflow: hidden;
    background: var(--page);
    font-family: "Arimo", Arial, sans-serif;
  }
  .card {
    position: absolute; left: 260px; width: 680px; height: 388px;
    overflow: hidden; border-radius: 3px;
  }
  .card-front { top: 70px; background: var(--card); }
  .card-back { top: 505px; background: var(--card-back); }

  .brand { position: absolute; display: flex; align-items: center; gap: 12px; white-space: nowrap; }
  .brand-mark { width: 30px; height: 30px; background: var(--red); flex: none; }
  .brand-name { font-weight: 700; font-size: 34px; letter-spacing: 1px; color: var(--white); line-height: 1; }
  .brand-tagline {
    position: absolute; font-size: 13px; letter-spacing: 5px; color: var(--text); white-space: nowrap;
  }
  .card-front .brand { left: 200px; top: 44px; }
  .card-front .brand-tagline { left: 180px; top: 92px; }

  .decor-circle {
    position: absolute; right: -60px; top: 110px; width: 360px; height: 360px;
    border-radius: 50%; background: var(--faint);
  }

  .holder { position: absolute; left: 48px; top: 205px; }
  .holder-name { font-size: 22px; color: var(--red); letter-spacing: 0.5px; }
  .holder-title { font-size: 17px; color: var(--text); margin-top: 4px; }

  .contacts {
    position: absolute; left: 40px; bottom: 40px;
    display: flex; gap: 22px; align-items: center;
    font-size: 15px; color: var(--text);
  }
  .contact { display: flex; align-items: center; gap: 7px; white-space: nowrap; }
  .contact svg { width: 15px; height: 15px; flex: none; }

  .stripe { position: absolute; left: 0; right: 0; bottom: 0; height: 10px; display: flex; }
  .stripe span { flex: 1; }
  .stripe .s-red { background: var(--red); }
  .stripe .s-grey { background: var(--grey); }
  .stripe .s-white { background: var(--white); }

  .card-back .brand { left: 0; right: 0; top: 148px; justify-content: center; gap: 16px; }
  .card-back .brand-mark { background: var(--emboss); width: 40px; height: 40px; }
  .card-back .brand-name { color: var(--emboss); font-size: 46px; }
  .card-back .brand-tagline { left: 0; right: 0; top: 218px; text-align: center; color: var(--emboss); font-size: 15px; }
</style>
</head>
<body>

<section class="card card-front">
  <div class="decor-circle" aria-hidden="true"></div>

  <div class="brand">
    <span class="brand-mark"></span>
    <span class="brand-name">VORNAK SYSTEMS</span>
  </div>
  <p class="brand-tagline">A VORNAK GROUP DIVISION.</p>

  <div class="holder">
    <p class="holder-name">RAJESH PALLIVAL</p>
    <p class="holder-title">General Manager</p>
  </div>

  <div class="contacts">
    <span class="contact">
      <svg viewBox="0 0 16 16" aria-label="Mobile"><rect x="4" y="1" width="8" height="14" rx="1.5" fill="none" stroke="#e21b23" stroke-width="1.4"/><line x1="7" y1="12.5" x2="9" y2="12.5" stroke="#e21b23" stroke-width="1.2"/></svg>
      0097150738265
    </span>
    <span class="contact">
      <svg viewBox="0 0 16 16" aria-label="Office"><path d="M4 1.5 L6.5 4.5 L5 6.5 C6 9 7.5 10.5 9.5 11 L11.5 9.5 L14.5 12 L12.5 14.5 C7 14 2 9 1.5 3.5 Z" fill="#e21b23"/></svg>
      009714368547
    </span>
    <span class="contact">
      <svg viewBox="0 0 16 16" aria-label="Email"><rect x="1.5" y="3.5" width="13" height="9" fill="none" stroke="#e21b23" stroke-width="1.4"/><path d="M1.5 3.5 L8 9 L14.5 3.5" fill="none" stroke="#e21b23" stroke-width="1.4"/></svg>
      RAJESH@VORNAKSYS.EXAMPLE
    </span>
  </div>

  <div class="stripe"><span class="s-red"></span><span class="s-grey"></span><span class="s-white"></span></div>
</section>

<section class="card card-back">
  <div class="brand">
    <span class="brand-mark"></span>
    <span class="brand-name">VORNAK SYSTEMS</span>
  </div>
  <p class="brand-tagline">A VORNAK GROUP DIVISION.</p>
</section>

</body>
</html>
```